Chartered Professional Accounting Firm Needs a Business Card Design

We need a card design for an accounting firm based in Toronto, Ontario. The firm name is Pavel Ostrom Professional Corporation. The owner of the firm is a chartered professional accountant and a certified general accountant. Services of the firm include 60% tax preparation and consulting and 40% financial statements for corporation year-end. We would like a modern design. The color could be black, white, gray, blue or other color to bring more confidence to clients. The logo of the firm should be included in the design. Thanks

Name: Pavel Ostrom, CPA, CGA Address: 47 Maple Crest Rd. Richmond Hill, ON L7K 3B5 Telephone: (416) 562-3907 Fax:(416) 734-2165 Email: pavel@pavelostrom-example.ca

Accounting

```html
<!DOCTYPE html>
<html lang="en">
<head>
<meta charset="UTF-8">
<title>Pavel Ostrom Professional Corporation – Business Card</title>
<link href="https://fonts.googleapis.com/css2?family=Michroma&display=swap" rel="stylesheet">
<style>
  :root {
    --bg: #d8d2c8;
    --card-white: #ffffff;
    --card-blue: #33379a;
    --text-light: #ffffff;
    --text-soft: #d5d7f0;
    --brand-blue: #33379a;
    --tag-grey: #7a7a80;
  }
  * { margin: 0; padding: 0; box-sizing: border-box; }
  html, body {
    width: 1200px;
    height: 800px;
    overflow: hidden;
    background: var(--bg);
    font-family: "Michroma", sans-serif;
  }
  .canvas {
    position: relative;
    width: 1200px;
    height: 800px;
  }
  .card {
    position: absolute;
    left: 150px;
    top: 143px;
    width: 900px;
    height: 514px;
    display: flex;
    box-shadow: 0 18px 40px rgba(0,0,0,0.25);
  }
  .card-brand {
    width: 380px;
    background: var(--card-white);
    display: flex;
    align-items: center;
    padding-left: 48px;
    gap: 14px;
  }
  .brand-mark {
    flex: none;
  }
  .brand-text {
    display: flex;
    flex-direction: column;
    gap: 5px;
  }
  .brand-name {
    color: var(--brand-blue);
    font-size: 13px;
    line-height: 1.35;
    text-transform: uppercase;
    letter-spacing: 0.5px;
  }
  .brand-tagline {
    color: var(--tag-grey);
    font-size: 6.5px;
    letter-spacing: 0.6px;
    text-transform: uppercase;
    line-height: 1.5;
  }
  .card-contact {
    flex: 1;
    background: var(--card-blue);
    color: var(--text-light);
    padding: 108px 0 0 64px;
  }
  .holder-name {
    font-size: 22px;
    letter-spacing: 1px;
    text-transform: uppercase;
  }
  .holder-credentials {
    font-size: 12px;
    color: var(--text-soft);
    letter-spacing: 1px;
    margin-top: 2px;
  }
  .contact-list {
    list-style: none;
    margin-top: 44px;
  }
  .contact-item {
    display: flex;
    align-items: flex-start;
    gap: 22px;
    font-size: 15px;
    letter-spacing: 1px;
    line-height: 1.45;
    margin-bottom: 9px;
  }
  .contact-icon {
    flex: none;
    width: 24px;
    height: 20px;
    margin-top: 1px;
    fill: var(--text-light);
  }
</style>
</head>
<body>
<main class="canvas">
  <article class="card">
    <section class="card-brand">
      <svg class="brand-mark" width="34" height="34" viewBox="0 0 34 34" aria-hidden="true">
        <circle cx="17" cy="17" r="16" fill="var(--brand-blue)"/>
      </svg>
      <div class="brand-text">
        <p class="brand-name">Pavel Ostrom<br>Professional Corporation</p>
        <p class="brand-tagline">Chartered Professional Accountant<br>Certified General Accountant</p>
      </div>
    </section>

    <section class="card-contact">
      <h1 class="holder-name">Pavel Ostrom</h1>
      <p class="holder-credentials">CPA, CGA</p>

      <ul class="contact-list">
        <li class="contact-item">
          <svg class="contact-icon" viewBox="0 0 24 20" aria-label="Telephone">
            <path d="M2 8c0-3 4-5 10-5s10 2 10 5v2h-5V8h-2v2H9V8H7v2H2z"/>
            <path d="M6 11h12l2 7H4z"/>
          </svg>
          <span>(416) 562-3907</span>
        </li>
        <li class="contact-item">
          <svg class="contact-icon" viewBox="0 0 24 20" aria-label="Fax">
            <rect x="6" y="1" width="12" height="5"/>
            <rect x="1" y="7" width="22" height="8" rx="1"/>
            <rect x="6" y="13" width="12" height="6"/>
          </svg>
          <span>(416) 734-2165</span>
        </li>
        <li class="contact-item">
          <svg class="contact-icon" viewBox="0 0 24 20" aria-label="Email">
            <path d="M2 3h20v14H2z M4 5v1l8 6 8-6V5l-8 6z" fill-rule="evenodd"/>
          </svg>
          <span>pavel@pavelostrom-example.ca</span>
        </li>
        <li class="contact-item">
          <svg class="contact-icon" viewBox="0 0 24 20" aria-label="Address">
            <path d="M12 1l11 9h-3v9h-6v-6h-4v6H4v-9H1z"/>
          </svg>
          <span>47 Maple Crest Rd. Richmond Hill,<br>ON L7K 3B5</span>
        </li>
      </ul>
    </section>
  </article>
</main>
</body>
</html>
```